Systems and Technology Consultants - Website

Design & Build a website for a new company which operates in the Systems and Technology space for Transportation, Government and Commercial sectors.

Overall design should be minimalist in nature.
Should also have a feed that provides news and event updates on the main page.
Logo has already been awarded and should be incorporated into the site.

We like the overall layout, functionality and simplicity of the below sites. Submitted designs could be similar to or a combination of the aspects on these sites, or perhaps a whole different concept - we are open to new ideas.
Norvique.com
Teblo.it

Update 1 Dated 27 May 2014

All I am moving away from the Teblo.it website and would like it to be more aligned with Norvique.com not only in layout but in functionality. I will be extending the deadline of this design brief for two weeks to incorporate additional requirements and will add addtional funding to the project.

Apologies for not having more information available to provide but with so many submissions its getting confusing.

Thanks Derek

Please note that the brief has been updated and the deadline has been extended.

Important: We will need two language versions of the website, English and Arabic; the website is hosted on HostPelican

Hello All, Thank you for your submissions. We have narrowed it down to the final 6 designers and I just wanted to take a moment and provide a bit of feedback regarding the concepts that we like and the modifications we are looking for. First, let me mention some of the design functions we like. - At the top of the homepage we really like the "region" or "language" tab so that the website can be viewed in both English and Arabic. - We like the homepage to have clear color variation so that the different sections of the homepage are distinct. Additionally, we like the bottom portion of the homepage to be in red. We feel that draws attention to our contact information. Again, we would like the colors to integrate black, gray-scale, red, etc. - Having a search tab at the top of the home page, or integrated into the main image, so that the site is easy to navigate. - We especially like the main image to have the scrolling tabs at the bottom so it is easy to browse the services offered (Consultancy, Solutions Architecture, Masters Systems Integration, Independent Design Review). - In regards to the services offered tab we really like the idea that a few people presented that have the outside of our logo with an icon in the middle of consultancy, solutions, etc., etc. Secondly, as mentioned in our brief we really enjoy the design of norvique site. Specially, we enjoy the strong iconic images they use, the way the tabs at the top scroll easily, and contact us page that generates an email. Lastly, I've included some photos of the concept we have been working on. What we are trying to demonstrate is how our company offers a range of services that are essentially linked together. We provide individual services that when combined present the full service package. We would like this concept to be integrated into the over concept of our website. Please feel free to ask for clarification of any of the above points or contact us if you have any additional questions. We appreciate all of your hard work and are very excited to see the updated designs. Best, Marta Vennick Quelbrant Senior Program Manager marta.vennick@quelbrant-example.com

Industry/Entity Type

Government

Font styles to use
Serif
Sans Serif

Requirements
Must have
• Must work on/adapt to various/mobile devices (responsive)
Must be simple and straightforward
Colors should be in line/matching with logo
2 language versions: English and Arabic (no Thai)
Services should be the first group/row of items after/below the main image
Note: the website will be hosted by hostpelican
Nice to have
• Submit feedback form
What's New section
The banner at the bottom of the site should not be too large; we would like a narrow one more
It would be nice if the header/top banner (with Home, About, etc. tabs) could stay in place as you scroll down (like Norvique and Chatterloop)
We will likely only use one image with a Company slogan on the Home page rather than a carousel of images to rotate through
Should not have
• This is the existing website: http://www.quelbrant-example.org
We do not like the animation, the way the banner icons/titles bounce
Not simple enough, we don't like the functionality or how pages load so slowly
We do not like the logo centered - it should be at the left
The banner and its tabs should not be towards the right, we would like them to be centered, to go all the way across and to be below the logo

```html
<!DOCTYPE html>
<html lang="en">
<head>
<meta charset="utf-8">
<title>Quelbrant International – Home</title>
<link href="https://fonts.googleapis.com/css2?family=Ubuntu:wght@300;400;500&display=swap" rel="stylesheet">
<style>
:root{
  --red:#e31b23;
  --red-dark:#a4141c;
  --ink:#333333;
  --grey:#8a8a8a;
  --grey-light:#b5b5b5;
  --line:#e4e4e4;
  --footer:#353535;
  --footer-base:#2d2d2d;
  --footer-text:#d6d6d6;
  --white:#ffffff;
}
*{box-sizing:border-box;margin:0;padding:0}
html,body{width:1200px;height:1200px;overflow:hidden;background:var(--white)}
body{position:relative;font-family:"Ubuntu",Arial,sans-serif;color:var(--ink)}
.abs{position:absolute}

/* header */
.site-header{position:absolute;left:0;top:0;width:1200px;height:75px;background:var(--white);border-bottom:3px solid var(--red)}
.brand{left:175px;top:18px;display:flex;align-items:center;gap:12px}
.brand-dot{width:34px;height:34px;border-radius:50%;border:4px solid var(--red)}
.brand-name{color:var(--red);font-weight:500;line-height:1}
.brand-name .l1{display:block;font-size:19px;letter-spacing:4px}
.brand-name .l2{display:block;font-size:11px;letter-spacing:3.2px;margin-top:4px}
.region{left:745px;top:14px;font-size:11px;color:var(--grey-light);display:flex;gap:6px;align-items:center}
.region .on{color:var(--red)}
.region .pin{width:8px;height:8px;border-radius:50%;background:var(--red)}
.search{left:904px;top:14px;width:124px;height:18px;display:flex;align-items:center}
.search-field{width:110px;height:16px;background:#f1f1f1;border:1px solid #e2e2e2;border-radius:8px;font-size:10px;color:#c8c8c8;padding-left:6px;line-height:14px}
.search-btn{width:18px;height:18px;border-radius:50%;background:var(--red);margin-left:-4px}
.main-nav{left:0;top:44px;width:1200px;height:18px;font-size:12.5px;color:var(--grey-light)}
.main-nav span{position:absolute;top:0;white-space:nowrap}
.main-nav .current{color:var(--red);font-weight:500}
.social{display:flex;gap:4px}
.social i{display:block;width:18px;height:18px;border-radius:50%;background:#d4d4d4}
.social i.hot{background:var(--red)}
.header-social{left:966px;top:44px}

/* hero */
.hero{left:0;top:75px;width:1200px;height:370px;background:linear-gradient(180deg,#b51820 0%,#c61c24 45%,#9e141b 100%)}
.hero-photo{left:150px;top:0;width:440px;height:370px;background:radial-gradient(ellipse at 45% 55%,#d9c2c8 0%,#6b5a66 35%,#262228 75%,#1c1a1e 100%)}
.hero-tagline{right:192px;top:60px;color:var(--white);font-size:17px;font-weight:500;text-align:right}
.hero-badge{left:659px;top:121px;width:128px;height:128px;border-radius:50%;background:var(--white)}
.hero-name{left:802px;top:162px;width:206px;color:var(--white);font-weight:500;line-height:1}
.hero-name .l1{display:block;font-size:25px;letter-spacing:3.5px}
.hero-name .l2{display:block;font-size:13px;letter-spacing:3.6px;margin-top:8px;padding-left:22px}
.hero-copy{right:192px;top:286px;color:var(--white);font-size:16px;font-weight:400;text-align:right;line-height:19px}

/* content */
.section-title{font-size:24px;font-weight:400;color:var(--red)}
.welcome-title{left:197px;top:485px}
.welcome-text{left:198px;top:519px;width:384px;font-size:12.5px;line-height:14.5px;color:#666;font-weight:400}
.welcome-text p{margin-bottom:14px}
.divider{left:598px;top:522px;width:1px;height:270px;background:var(--line)}
.services-title{left:621px;top:485px}
.service-tile{width:126px;height:121px;border:1px solid var(--line);background:var(--white);display:flex;flex-direction:column;align-items:center;justify-content:flex-start;padding-top:32px;text-align:center;font-size:12px;line-height:14px;color:var(--grey-light)}
.service-tile svg{margin-bottom:6px}
.service-tile.active{background:var(--red);color:var(--white);border-color:var(--red);box-shadow:0 2px 4px rgba(0,0,0,.25)}

/* footer */
.site-footer{left:0;top:828px;width:1200px;height:310px;background:var(--footer)}
.footer-head{font-size:14px;color:var(--white);font-weight:500;border-bottom:1px solid #4a4a4a;padding-bottom:8px;display:flex;justify-content:space-between;align-items:center}
.links{left:196px;top:870px;width:236px}
.links ul{list-style:none;margin-top:5px;font-size:11px;color:var(--footer-text);line-height:18.9px}
.links .u{text-decoration:underline;color:var(--white)}
.events{left:472px;top:870px;width:236px}
.event{border-bottom:1px solid #4a4a4a;padding:7px 0 8px 2px;font-size:10.5px;color:#c4c4c4;line-height:12.5px}
.event-top{display:flex;justify-content:space-between;color:var(--white);font-size:11px;margin-bottom:2px;letter-spacing:.3px}
.event-link{text-align:right;color:var(--white);font-size:11px;margin-top:20px}
.contact{left:771px;top:870px;width:237px}
.footer-brand{margin-top:9px;color:var(--white);font-size:14px;letter-spacing:4px;font-weight:500;display:flex;align-items:center;gap:8px}
.footer-brand i{display:block;width:18px;height:18px;border:2px solid var(--white);border-radius:50%}
.notify{margin-top:24px;display:flex;height:26px;width:240px}
.notify-field{flex:1;background:var(--white);border-radius:13px 0 0 13px;font-size:11px;color:#555;padding:7px 0 0 14px}
.notify-btn{width:68px;background:var(--red);border-radius:13px;color:var(--white);font-size:11px;text-align:center;padding-top:6px;margin-left:-8px}
.contact-line{display:flex;align-items:center;gap:8px;font-size:11px;color:var(--white);margin-top:8px;letter-spacing:.2px}
.contact-line.first{margin-top:16px}
.contact-line .ico{width:17px;height:17px;border-radius:50%;background:var(--red);display:flex;align-items:center;justify-content:center}
.footer-social{margin-top:18px}
.footer-social i{background:#555}
.footer-social i.hot{background:var(--red)}
.footer-base{left:0;top:1138px;width:1200px;height:62px;background:var(--footer-base)}
.copyright{left:192px;top:1163px;font-size:10px;color:#9a9a9a}
.share-badge{left:940px;top:1161px;display:flex;gap:4px}
.share-badge .a{width:28px;height:18px;background:var(--red);border-radius:2px}
.share-badge .b{width:36px;height:18px;background:#eee;border-radius:2px;font-size:9px;color:#333;text-align:center;line-height:18px}
</style>
</head>
<body>

<header class="site-header">
  <div class="abs brand"><span class="brand-dot"></span><span class="brand-name"><span class="l1">QUELBRANT</span><span class="l2">INTERNATIONAL</span></span></div>
  <div class="abs region"><span class="pin"></span>Region: <span class="on">English</span>/ <span lang="ar">العربية</span></div>
  <div class="abs search"><span class="search-field">Search</span><span class="search-btn"></span></div>
  <nav class="abs main-nav">
    <span class="current" style="left:454px">Home</span>
    <span style="left:523px">Business Unit</span>
    <span style="left:629px">Services ▾</span>
    <span style="left:714px">About Us</span>
    <span style="left:798px">Locations</span>
    <span style="left:884px">Contact Us</span>
  </nav>
  <div class="abs social header-social"><i class="hot"></i><i></i><i></i></div>
</header>

<section class="abs hero">
  <div class="abs hero-photo" role="img" aria-label="Businessman holding a laptop, tablet, phone and connected globe in open hands"></div>
  <p class="abs hero-tagline">Integrated Systems, Reliable Solutions</p>
  <div class="abs hero-badge"></div>
  <p class="abs hero-name"><span class="l1">QUELBRANT</span><span class="l2">INTERNATIONAL</span></p>
  <p class="abs hero-copy">Quelbrant Int. specializes in delivering quality professional services and<br>technical projects that support larger business goals.</p>
</section>

<h2 class="abs section-title welcome-title">Welcome</h2>
<div class="abs welcome-text">
  <p>Quelbrant specializes in delivering quality professional services and technical projects that support larger business goals. systems are tools that support a greater business function and need. we understand that most technical projects are conceptualized to support a larger vision with actual business goals in mind and ensure that all of our professional and certified expertise is included in our professional services to meet those goals.</p>
  <p>quelbrant recognizes the middle east and greater asia regions are economic growth markets with developing infrastructure projects requiring specialist systems and technical expertise. accordingly, quelbrant has evolved its presence in the regions to meet client demands and expectations.</p>
  <p>our ultimate goal is to provide quality, technical and professional services on projects of any scale and/or complexity, from conception through to completion. our philosophy is simple; stick to what you are good at and be the best at it.</p>
</div>
<div class="abs divider"></div>

<h2 class="abs section-title services-title">Services</h2>
<div class="abs service-tile" style="left:619px;top:523px">
  <svg width="36" height="36" viewBox="0 0 36 36" fill="#c4c4c4"><circle cx="8" cy="6" r="3"/><circle cx="18" cy="6" r="3"/><circle cx="28" cy="6" r="3"/><rect x="5" y="11" width="26" height="4"/><rect x="4" y="17" width="28" height="4"/><circle cx="8" cy="26" r="3"/><circle cx="28" cy="26" r="3"/><rect x="16" y="21" width="4" height="12"/></svg>
  CONSULTANCY
</div>
<div class="abs service-tile active" style="left:753px;top:523px">
  <svg width="46" height="36" viewBox="0 0 46 36" fill="none" stroke="#fff" stroke-width="2.5"><path d="M3 34h40M6 34V8h10v26M20 34V4h10v30M34 34V14h8v20M9 14h4M9 20h4M23 10h4M23 16h4M23 22h4"/></svg>
  SOLUTIONS<br>ARCHITECTURE
</div>
<div class="abs service-tile" style="left:886px;top:523px;padding-top:12px">
  <svg width="54" height="56" viewBox="0 0 54 56" fill="#c4c4c4" stroke="#c4c4c4" stroke-width="1.5"><circle cx="27" cy="28" r="9"/><circle cx="27" cy="4" r="3"/><circle cx="6" cy="40" r="3"/><circle cx="48" cy="40" r="3"/><circle cx="46" cy="12" r="3"/><circle cx="27" cy="52" r="3"/><path d="M27 7v12M9 38l10-6M45 38l-10-6M44 14l-10 8M27 37v12"/></svg>
  MASTERS SYSTEMS<br>INTEGRATION
</div>
<div class="abs service-tile" style="left:619px;top:655px">
  <svg width="38" height="36" viewBox="0 0 38 36" fill="none" stroke="#c4c4c4" stroke-width="2.5"><rect x="12" y="3" width="23" height="18"/><circle cx="6" cy="9" r="3" fill="#c4c4c4"/><path d="M6 14v20M2 18h12M17 14l5-5 4 4 6-6"/></svg>
  INDEPENDENT<br>DESIGN REVIEW
</div>

<footer class="abs site-footer"></footer>

<div class="abs links">
  <div class="footer-head">Interesting Links
    <svg width="16" height="16" viewBox="0 0 16 16" fill="none" stroke="#fff" stroke-width="2"><rect x="1.5" y="7" width="7" height="5" rx="2.5" transform="rotate(-45 5 9.5)"/><rect x="7.5" y="3.5" width="7" height="5" rx="2.5" transform="rotate(-45 11 6)"/></svg>
  </div>
  <ul>
    <li>Lorem ipsum</li><li class="u">Lorem ipsum Dolor</li><li>Lorem ipsum Sit</li><li>Lorem ipsum</li><li>Lorem ipsum ampet</li><li>Dolor sit</li><li>Sit ampet</li><li>Dolor sit ampet</li>
  </ul>
</div>

<div class="abs events">
  <div class="footer-head">Upcoming Events
    <svg width="18" height="16" viewBox="0 0 18 16" fill="none" stroke="#fff" stroke-width="1.6"><rect x="1" y="2" width="13" height="12"/><path d="M1 6h13M4 0v3M11 0v3"/><circle cx="13" cy="12" r="3" fill="#353535"/></svg>
  </div>
  <div class="event">
    <div class="event-top"><span>Lorem ipsum</span><span>11-22-2014</span></div>
    Ut wisi enim ad minim veniam, quis nostrud exerci tation ullamcorper suscipit lobortis nisl ut aliquip ex ea commodo consequat.
    <div class="event-link">Go to Event</div>
  </div>
  <div class="event">
    <div class="event-top"><span>Lorem ipsum</span><span>11-22-2014</span></div>
    Duis autem vel eum iriure dolor in hendrerit in vulputate velit esse molestie consequat, vel illum dolore eu feugiat nulla facilisis at vero eros et accumsan ...
    <div class="event-link" style="margin-top:3px">Go to Event</div>
  </div>
</div>

<div class="abs contact">
  <div class="footer-head">Contact Us
    <svg width="16" height="16" viewBox="0 0 16 16" fill="none" stroke="#fff" stroke-width="1.6"><rect x="3" y="1" width="11" height="14"/><path d="M1 4h3M1 8h3M1 12h3"/><circle cx="8.5" cy="7" r="2"/></svg>
  </div>
  <div class="footer-brand"><i></i>QUELBRANT</div>
  <div class="notify"><span class="notify-field">type your email to get notify</span><span class="notify-btn">submit</span></div>
  <div class="contact-line first"><span class="ico"><svg width="9" height="9" viewBox="0 0 10 10" fill="#fff"><path d="M2 0l2 2.5-1 1.2c.6 1.3 1.6 2.3 2.9 2.9l1.2-1L10 7.7 8.5 10C4 9.6.4 6 0 1.5z"/></svg></span>Phone numbers: +(00)-01-555-0142-7</div>
  <div class="contact-line"><span class="ico"><svg width="9" height="7" viewBox="0 0 10 8" fill="none" stroke="#fff" stroke-width="1.3"><rect x=".5" y=".5" width="9" height="7"/><path d="M.5 .5l4.5 4 4.5-4"/></svg></span>Email: info@quelbrant-example.org</div>
  <div class="social footer-social" style="gap:7px"><i></i><i></i><i class="hot"></i></div>
</div>

<div class="abs footer-base"></div>
<p class="abs copyright">Copyright 2005-2014 &nbsp;www.quelbrant-example.biz All rights reserved.</p>
<div class="abs share-badge"><span class="a"></span><span class="b">3,450</span></div>

</body>
</html>
```